Blood Testing Health App

We are looking for a graphics designer to create a web app for us so that we may insert it into a health management website system.
For branding purposes we are at www.Vantiqor.com and we are revamping our website... Example of new colors attached.
How we work...
We are a blood testing company based in the USA.
We offer a blood testing service nationwide in the USA.
We allow customers to order tests directly from us, visit a lab, have their blood drawn, or submit a urine sample, the lab tests it and they send the results back to our computer system and we share it with the customer.
The benefits of this are the customer does not need to go to the doctor and pay for the doctors visit to order these tests, which save them money. The tests are cheaper than going through the doctor. The customer simply uses us to get the test and the results and they can then take the results to their doctor... this process has saved them money. Others may be interested in regular check ups for blood work etc... and this allows them to do it with out needing a doctor, or if you have no insurance, this is a cheaper option too. We are quicker than a doctor, customers do not need appointments etc.
Hopefully you now have a better understanding as to what we do.
Here is the spec.
The app screen size is 750 px wide by 700 px high. ( A pdf is attached to show where the app is going to go, it is on page 3 of the pdf) The customer will have the ability to scroll… therefore the length of the page can be longer.
The app will consist of the following sections
Entry Page –
This will be the first page the user sees upon opening the app. This will be where they are directed from to the sections of the app discussed below. This needs to be branded for VantiQor with a modern look.
1 – Order Test (Giving them the ability to purchase a blood test within the app)
2 – VantiQor Dashboard (A dashboard that has everything they could need to use our service_
How it works Section on entry page – this will be a simple set of graphics showing how the service works. We already have the graphics for this, they do not need to be built again. They are attached to this brief
Basic structure of sections –
Order Test –
This page contains all tests, filed in categories – and Sub categories – Each test needs a link to an Information section – Price – Buy Now – Cart Process
VantiQor Dashboard –
A page of icons along the top of the app
- My Confirmation
- My Nearest Lab
- My Receipt
- My Orders
- My Account
- My Results
- My Inbox
- Contact Us
Sections in more detail -
Order A Test –
Show all categories/ sub categories – There are 23 categories, 14 sub categories, and within these categories are 300 tests - Here is the information for the categories etc - http://www.vantiqor.com/panels.aspx?PanelGroupID=4 Just in case it helps :)
We need to present this in a graphic format that is spacious, modern (brimlake, kivvo web appearance is the direction we are going for) We need it to be clear and not overwhelming to the customer.
Functionality idea…
Customer clicks category/ subcategory and tests appear.
Customer sees small 35 word description. For more information the test opens into a lightbox or expand the container which ever graphic designer believes to be most visually appealing
Buy Now must always be visible, along with price of the test
Buying process explained – Customer clicks buy now –
They are then taken to a Review Order screen ( This contains Order summary and choose payment method – insert payment details )
– Confirm payment –
Confirmation screen appears, thanking them.
They are then taken to the VantiQor Dashboard...
VantiQor Dashboard –
"My Confirmation" - Print Confirmation Order (PDF is in brief, we want this web based not a pdf download)
"My Nearest Lab Location" - This does not need to be designed because the web developer has this part under control, but we do need the icon in the dashboard
"My Receipt" - Print receipt - This does not exist in our system yet. So we need to create this from scratch - It will need to have - The test they are purchasing and the amount of the test - The customers name - The order ID - Must provide printer friendly option too
"My Orders" - This will have a list of orders - At the end of each order will be a status update of either "Test results" "Open order"
A graphic table format would be perfect. This will be linked to relevant results if they have been received. I have also attached a version of what the customer currently sees on our website. We know it is nasty ;) We are redesigning... but the information is there for this section to help design it with the right info. If the results are ready it will say in this list.
"Results Ready" will be a link to show those results once the customer has clicked the link, and the results will appear in the app, under the icons. There must be a printer friendly version too.
"My Results" Developer will sort this page out but we need the icon... It will be exactly like my orders but only show test results
"My Account" - This will be a place for them to update their personal information - Name, DOB, Address, Email Address
"My Inbox" - An inbox interface - Our way of contacting the customer for promotions we are running etc – We need a design of how this screen will appear. We also need the icon in the dashboard to have a notification on it if there are messages in the customers inbox. A little red 1, or circle with number of messages in the inbox.
"Customer Service" - This does not need to be designed because the web developer has this part under control, but we do need the icon in the dashboard
Icons appear along the top of app ( example - Mac icons/ iphone app icons) When the customer clicks an icon the content always appears below the icons
Here is more information for the icons and what should appear when each icon is clicked.
Screens to be designed –
Entry Page
Order A Test Page
Review Order Screen/Payment Screen - Show a lightbox that shows payment has been confirmed. Customer clicks close and are on the Confirmation Screen
VantiQor Dashboard - Screens mentioned in detail above
We can't wait to see your designs!
Please email any questions.
Hi all this is the first time we have used pixel harbor and understand the budget was too low for this project. We have now increased the budget to $2,000 and extended the deadline by another week
Hi all we are receiving some really great designs. I just added an example of the space that the web app will be going into... It is called "morvelapp.pdf"
Hi guys updated the brief. Hopefully this will help with the dashboard part of the design

```html
<!DOCTYPE html>
<html lang="en">
<head>
<meta charset="utf-8">
<title>VantiQor Dashboard – My Inbox</title>
<link href="https://fonts.googleapis.com/css2?family=Open+Sans:wght@400;600;700&display=swap" rel="stylesheet">
<style>
  :root{
    --green:#7cbf37;
    --ink:#333333;
    --brand-ink:#3a3a3a;
    --grey-text:#9a9a9a;
    --band:#e6e6e6;
    --panel:#e8e8e8;
    --table-head:#545955;
    --row-line:#e4e4e4;
    --white:#ffffff;
    --blue:#2d7ec4;
    --badge:#f04a24;
    --icon:#5a5a5a;
  }
  *{box-sizing:border-box;margin:0;padding:0}
  html,body{width:1091px;height:1200px;overflow:hidden;background:var(--white)}
  body{font-family:"Open Sans",Arial,sans-serif;color:var(--ink)}
  .app{width:750px;height:825px;position:relative;transform:scale(1.4547);transform-origin:0 0}

  /* header */
  .site-header{position:absolute;left:0;top:0;width:750px;height:100px;background:var(--white)}
  .brand-name{position:absolute;left:18px;top:48px;font-size:36px;font-weight:400;color:var(--brand-ink);letter-spacing:1px;line-height:40px}
  .tab{position:absolute;top:29px;height:71px;text-align:center;font-size:11px;text-transform:uppercase}
  .tab svg{display:block;margin:12px auto 6px}
  .tab-order{left:352px;width:96px;color:var(--grey-text)}
  .tab-dashboard{left:456px;width:124px;background:var(--band);border-radius:6px 6px 0 0;color:var(--green)}
  .social{position:absolute;top:63px;left:627px;display:flex;gap:10px}
  .social span{width:28px;height:28px;border-radius:50%;background:var(--green)}

  /* icon nav */
  .dash-nav{position:absolute;left:0;top:100px;width:750px;height:136px;background:linear-gradient(var(--band),#e2e2e2)}
  .dash-nav ul{list-style:none;position:relative;height:100%}
  .nav-item{position:absolute;top:30px;width:96px;margin-left:-48px;text-align:center;font-size:12px;color:var(--ink);line-height:12px}
  .nav-item .bubble{width:62px;height:62px;margin:0 auto 8px;border-radius:50%;background:radial-gradient(circle at 50% 35%,#ffffff,#e4e4e4 70%,#cfcfcf);box-shadow:0 2px 3px rgba(0,0,0,.25);display:flex;align-items:center;justify-content:center;position:relative}
  .nav-item .glyph{width:34px;height:34px;border-radius:50%;background:#6a6a6a}
  .nav-item.is-active{color:var(--blue)}
  .badge{position:absolute;right:-4px;top:2px;width:22px;height:18px;border-radius:4px;background:var(--badge);color:var(--white);font-size:10px;font-weight:600;line-height:18px}
  .nav-pointer{position:absolute;left:592px;top:226px;width:0;height:0;border-left:9px solid transparent;border-right:9px solid transparent;border-bottom:10px solid var(--white)}

  /* inbox */
  .inbox-frame{position:absolute;left:17px;top:262px;width:716px;height:540px;background:var(--panel);border-radius:8px}
  .inbox{position:absolute;left:12px;top:13px;width:688px;height:512px;background:var(--white);border-radius:7px;overflow:hidden}
  .inbox-head{height:47px;background:var(--green);position:relative}
  .inbox-title{position:absolute;left:15px;top:11px;font-size:18px;color:var(--white);font-weight:400}
  .inbox-actions{position:absolute;right:15px;bottom:0;display:flex;gap:3px}
  .inbox-actions span{background:var(--table-head);color:var(--white);font-size:10px;height:23px;line-height:23px;padding:0 10px;border-radius:4px 4px 0 0;display:flex;align-items:center;gap:6px}
  .messages{list-style:none}
  .msg{display:flex;align-items:center;height:35px;border-bottom:1px solid var(--row-line);font-size:13px;color:var(--ink)}
  .msg:last-child{border-bottom:none}
  .msg-head{height:37px;background:var(--table-head);color:var(--white);border-bottom:none}
  .col-check{width:75px;padding-left:25px;flex:none}
  .col-title{width:487px;flex:none;white-space:nowrap;overflow:hidden}
  .col-date{font-size:11px;padding-left:2px}
  .msg-head .col-date{font-size:13px}
  .checkbox{display:block;width:16px;height:16px;border:1px solid #c4c4c4;background:#f2f2f2;border-radius:2px}
  .msg-head .checkbox{background:#6d716e;border-color:#a9aca9}
  .is-unread .col-title{font-weight:700}
</style>
</head>
<body>
<div class="app">
  <header class="site-header">
    <span class="brand-name">VANTIQOR</span>
    <div class="tab tab-order">
      <svg width="26" height="20" viewBox="0 0 26 20"><rect x="4" y="1" width="18" height="13" rx="2" fill="#a8a8a8"/><rect x="1" y="15" width="24" height="3" rx="1" fill="#a8a8a8"/></svg>
      Order a test
    </div>
    <div class="tab tab-dashboard">
      <svg width="24" height="22" viewBox="0 0 24 22"><rect x="6" y="1" width="17" height="13" fill="none" stroke="#7cbf37" stroke-width="2"/><rect x="1" y="7" width="17" height="13" fill="#e6e6e6" stroke="#7cbf37" stroke-width="2"/></svg>
      Dashboard
    </div>
    <div class="social"><span></span><span></span><span></span></div>
  </header>

  <nav class="dash-nav">
    <ul>
      <li class="nav-item" style="left:47px"><div class="bubble"><svg width="34" height="30" viewBox="0 0 34 30"><rect x="2" y="2" width="30" height="20" rx="2" fill="none" stroke="#5a5a5a" stroke-width="3"/><polyline points="7,13 12,13 15,7 19,18 22,12 27,12" fill="none" stroke="#5a5a5a" stroke-width="2"/><rect x="12" y="24" width="10" height="4" fill="#5a5a5a"/></svg></div>My<br>Confirmation</li>
      <li class="nav-item" style="left:140px"><div class="bubble"><span class="glyph" role="img" aria-label="Microscope icon"></span></div>My<br>Nearest Lab</li>
      <li class="nav-item" style="left:234px"><div class="bubble"><span class="glyph" role="img" aria-label="DNA strand icon"></span></div>My Orders</li>
      <li class="nav-item" style="left:327px"><div class="bubble"><svg width="28" height="34" viewBox="0 0 28 34"><rect x="2" y="4" width="24" height="28" rx="2" fill="none" stroke="#5a5a5a" stroke-width="3"/><rect x="9" y="1" width="10" height="6" fill="#5a5a5a"/><polyline points="6,19 10,19 12,13 16,25 18,19 22,19" fill="none" stroke="#5a5a5a" stroke-width="2"/></svg></div>My Results</li>
      <li class="nav-item" style="left:419px"><div class="bubble"><svg width="28" height="34" viewBox="0 0 28 34"><rect x="2" y="4" width="24" height="28" rx="2" fill="none" stroke="#5a5a5a" stroke-width="3"/><rect x="9" y="1" width="10" height="6" fill="#5a5a5a"/><g fill="#5a5a5a"><rect x="6" y="12" width="3" height="3"/><rect x="11" y="12" width="11" height="3"/><rect x="6" y="18" width="3" height="3"/><rect x="11" y="18" width="11" height="3"/><rect x="6" y="24" width="3" height="3"/><rect x="11" y="24" width="11" height="3"/></g></svg></div>My Receipts</li>
      <li class="nav-item" style="left:512px"><div class="bubble"><span class="glyph" role="img" aria-label="Account figure icon"></span></div>My Account</li>
      <li class="nav-item is-active" style="left:606px"><div class="bubble"><svg width="36" height="26" viewBox="0 0 36 26"><rect x="1" y="1" width="34" height="24" fill="#2d7ec4"/><polyline points="1,1 18,15 35,1" fill="none" stroke="#bcd8f0" stroke-width="2"/></svg><span class="badge">2</span></div>My Inbox</li>
      <li class="nav-item" style="left:700px"><div class="bubble"><span class="glyph" role="img" aria-label="Support agent icon"></span></div>Contact Us</li>
    </ul>
  </nav>
  <span class="nav-pointer"></span>

  <section class="inbox-frame">
    <div class="inbox">
      <div class="inbox-head">
        <h1 class="inbox-title">MY MESSAGES</h1>
        <div class="inbox-actions">
          <span>mark as read <svg width="11" height="10" viewBox="0 0 11 10"><rect x=".5" y="1.5" width="8" height="8" fill="none" stroke="#fff"/><polyline points="2,5 4.5,7.5 10,1" fill="none" stroke="#fff" stroke-width="1.6"/></svg></span>
          <span>delete <b>x</b></span>
        </div>
      </div>
      <ul class="messages">
        <li class="msg msg-head"><span class="col-check"><span class="checkbox"></span></span><span class="col-title">Message Title</span><span class="col-date">Date</span></li>
        <li class="msg is-unread"><span class="col-check"><span class="checkbox"></span></span><span class="col-title">Lorem ipsum dolor sit amet, consectetur adipisicing elit</span><span class="col-date">Sep 13, 10:30 AM</span></li>
        <li class="msg is-unread"><span class="col-check"><span class="checkbox"></span></span><span class="col-title">Sed do eiusmod tempor incididunt ut labore et dolore magna aliqua.</span><span class="col-date">Sep 11, 02:10 AM</span></li>
        <li class="msg"><span class="col-check"><span class="checkbox"></span></span><span class="col-title">Ut enim ad minim veniam, quis nostrud exercitation ullamco laboris nisi...</span><span class="col-date">Sep 10, 12:54 PM</span></li>
        <li class="msg"><span class="col-check"><span class="checkbox"></span></span><span class="col-title">Duis aute irure dolor in reprehenderit in voluptate velit esse cillum dolore</span><span class="col-date">Sep 02, 12:23 AM</span></li>
        <li class="msg"><span class="col-check"><span class="checkbox"></span></span><span class="col-title">Lorem ipsum dolor sit amet, consectetur adipisicing elit</span><span class="col-date">Sep 13, 10:30 AM</span></li>
        <li class="msg"><span class="col-check"><span class="checkbox"></span></span><span class="col-title">Sed do eiusmod tempor incididunt ut labore et dolore magna aliqua.</span><span class="col-date">Sep 11, 02:10 AM</span></li>
        <li class="msg"><span class="col-check"><span class="checkbox"></span></span><span class="col-title">Ut enim ad minim veniam, quis nostrud exercitation ullamco laboris nisi...</span><span class="col-date">Sep 10, 12:54 PM</span></li>
        <li class="msg"><span class="col-check"><span class="checkbox"></span></span><span class="col-title">Duis aute irure dolor in reprehenderit in voluptate velit esse cillum dolore</span><span class="col-date">Sep 02, 12:23 AM</span></li>
        <li class="msg"><span class="col-check"><span class="checkbox"></span></span><span class="col-title">Lorem ipsum dolor sit amet, consectetur adipisicing elit</span><span class="col-date">Sep 13, 10:30 AM</span></li>
        <li class="msg"><span class="col-check"><span class="checkbox"></span></span><span class="col-title">Sed do eiusmod tempor incididunt ut labore et dolore magna aliqua.</span><span class="col-date">Sep 11, 02:10 AM</span></li>
        <li class="msg"><span class="col-check"><span class="checkbox"></span></span><span class="col-title">Ut enim ad minim veniam, quis nostrud exercitation ullamco laboris nisi...</span><span class="col-date">Sep 10, 12:54 PM</span></li>
        <li class="msg"><span class="col-check"><span class="checkbox"></span></span><span class="col-title">Duis aute irure dolor in reprehenderit in voluptate velit esse cillum dolore</span><span class="col-date">Sep 02, 12:23 AM</span></li>
      </ul>
    </div>
  </section>
</div>
</body>
</html>
```